Clean Vexlo Ads Banner Design For A Finance Company

Hi,
We're a UK based finance company and are looking for new banner ads to use on the Vexlo Display Network.
We want the end product to stand out by using strong, minimal design - ideally starting from a dark theme, although I'm open to ideas.
The copy should read:
'Fast Bridging Loans From 0.39% PM'
Once we have these designs agreed, we are looking to replicate them for other products, changing only the text on each ad - for example, 'commercial mortgage service you can rely on' or 'development finance service you can rely on'.
The colours used on our website are the following:
Black - #040303
Orange - #f79124
White - #ffffff
Grey - #ffffff
Example ads that I like - https://www.plimrake.com/wp-content/uploads/2021/07/vexlo-display-ads-example-2-final.png.webp
2 - https://qarnelvistahub.com/wp-content/uploads/2020/03/fbdd56ba3bd16c7a8debb13a411de786.jpg

```html
<!DOCTYPE html>
<html lang="en">
<head>
<meta charset="utf-8">
<title>Bridging Loan Banner Set</title>
<link rel="stylesheet" href="https://fonts.googleapis.com/css2?family=Poppins:wght@500;600;700&display=swap">
<style>
  :root {
    --page-bg: #f7f7f7;
    --ink: #0d0d0f;
    --orange: #f79124;
    --white: #ffffff;
    --label: #f0a040;
    --photo-dark: #2e323a;
    --photo-light: #c9ced6;
  }
  * { margin: 0; padding: 0; box-sizing: border-box; }
  html, body {
    width: 1200px;
    height: 899px;
    overflow: hidden;
    background: var(--page-bg);
    font-family: "Poppins", sans-serif;
  }
  .stage {
    position: relative;
    width: 936px;
    height: 701px;
    transform: scale(1.28205);
    transform-origin: 0 0;
  }
  .size-label {
    position: absolute;
    top: 27px;
    font-size: 12px;
    font-weight: 500;
    color: var(--label);
    letter-spacing: 0.3px;
  }
  .banner {
    position: absolute;
    display: block;
    box-shadow: 0 2px 6px rgba(0, 0, 0, 0.12);
  }
  .banner--rectangle { left: 28px; top: 54px; width: 336px; height: 280px; }
  .banner--skyscraper { left: 403px; top: 54px; width: 160px; height: 600px; }
  .banner--half-page { left: 601px; top: 54px; width: 300px; height: 600px; }

  .bg-dark { fill: var(--ink); }
  .panel-orange { fill: var(--orange); }
  .badge { fill: var(--white); }
  .headline { font-family: "Poppins", sans-serif; font-weight: 700; fill: var(--white); }
  .headline .accent { fill: var(--orange); }
  .offer { font-family: "Poppins", sans-serif; font-weight: 600; fill: var(--white); }
  .brand-name { font-family: "Poppins", sans-serif; font-weight: 700; fill: var(--orange); }
  .cta-pill { fill: var(--white); }
  .cta-label { font-family: "Poppins", sans-serif; font-weight: 600; fill: var(--orange); font-size: 12px; }
</style>
</head>
<body>
<div class="stage">
  <span class="size-label" style="left:32px">336 X 280</span>
  <span class="size-label" style="left:452px">160 X 600</span>
  <span class="size-label" style="left:720px">300 X 600</span>

  <!-- Medium rectangle -->
  <svg class="banner banner--rectangle" viewBox="0 0 336 280" xmlns="http://www.w3.org/2000/svg">
    <defs>
      <linearGradient id="photo-tone-a" x1="0" y1="0" x2="1" y2="1">
        <stop offset="0" stop-color="var(--photo-dark)"/>
        <stop offset="0.55" stop-color="#8d939c"/>
        <stop offset="1" stop-color="var(--photo-light)"/>
      </linearGradient>
    </defs>
    <rect class="bg-dark" width="336" height="280"/>
    <g role="img" aria-label="Photo of a business adviser reviewing financial charts at a desk">
      <polygon points="178,0 336,0 336,280 178,280" fill="url(#photo-tone-a)"/>
    </g>
    <path class="panel-orange" d="M0,161 H160 Q172,161 178,172 L232,280 H0 Z"/>
    <path class="badge" d="M187,0 H263 V50 L225,65 L187,50 Z"/>
    <text class="brand-name" x="225" y="33" font-size="15" text-anchor="middle">Corwell</text>
    <text class="headline" font-size="19" text-anchor="middle">
      <tspan x="81" y="54">Bridging</tspan>
      <tspan class="accent" x="81" y="83">Loan Service</tspan>
      <tspan x="81" y="112">You Can Rely</tspan>
      <tspan x="84" y="140">On</tspan>
    </text>
    <text class="offer" font-size="15" text-anchor="middle">
      <tspan x="81" y="199">5* Rated Service &amp;</tspan>
      <tspan x="83" y="225">No Broker Fees</tspan>
    </text>
    <rect class="cta-pill" x="39" y="242" width="84" height="23" rx="11.5"/>
    <text class="cta-label" x="81" y="258" text-anchor="middle">Click Here</text>
  </svg>

  <!-- Wide skyscraper -->
  <svg class="banner banner--skyscraper" viewBox="0 0 160 600" xmlns="http://www.w3.org/2000/svg">
    <defs>
      <linearGradient id="photo-tone-b" x1="0" y1="0" x2="1" y2="1">
        <stop offset="0" stop-color="var(--photo-dark)"/>
        <stop offset="0.5" stop-color="#8d939c"/>
        <stop offset="1" stop-color="var(--photo-light)"/>
      </linearGradient>
    </defs>
    <rect class="bg-dark" width="160" height="600"/>
    <g role="img" aria-label="Photo of hands holding a pen over financial reports and a calculator">
      <rect x="0" y="140" width="160" height="308" fill="url(#photo-tone-b)"/>
    </g>
    <polygon class="panel-orange" points="0,77 160,77 160,140 0,555"/>
    <text class="brand-name" x="80" y="48" font-size="32" text-anchor="middle">Corwell</text>
    <text class="headline" font-size="24">
      <tspan x="8" y="119">Bridging</tspan>
      <tspan x="8" y="159">Loan</tspan>
      <tspan x="8" y="199">Service</tspan>
      <tspan x="8" y="239">You Can</tspan>
      <tspan x="8" y="280">Rely</tspan>
      <tspan x="8" y="320">On</tspan>
    </text>
    <text class="offer" font-size="15" text-anchor="middle">
      <tspan x="83" y="496">5* Rated</tspan>
      <tspan x="84" y="522">Service &amp;</tspan>
      <tspan x="85" y="548">No Broker Fees</tspan>
    </text>
    <rect class="cta-pill" x="42" y="560" width="84" height="23" rx="11.5"/>
    <text class="cta-label" x="84" y="576" text-anchor="middle">Click Here</text>
  </svg>

  <!-- Half page -->
  <svg class="banner banner--half-page" viewBox="0 0 300 600" xmlns="http://www.w3.org/2000/svg">
    <defs>
      <linearGradient id="photo-tone-c" x1="0" y1="0" x2="1" y2="1">
        <stop offset="0" stop-color="var(--photo-dark)"/>
        <stop offset="0.5" stop-color="#8d939c"/>
        <stop offset="1" stop-color="var(--photo-light)"/>
      </linearGradient>
    </defs>
    <rect class="bg-dark" width="300" height="600"/>
    <g role="img" aria-label="Photo of business advisers discussing financial charts at a desk">
      <path d="M17,480 V285 Q17,262 38,252 L150,190 L262,252 Q287,262 287,285 V480 Z" fill="url(#photo-tone-c)"/>
    </g>
    <polygon class="badge" points="150,151 188,173 188,217 150,239 112,217 112,173"/>
    <text class="brand-name" x="150" y="201" font-size="17" text-anchor="middle">Corwell</text>
    <text class="headline" font-size="28" text-anchor="middle">
      <tspan x="150" y="46">Bridging</tspan>
      <tspan class="accent" x="150" y="84">Loan Service</tspan>
      <tspan x="153" y="122">You Can Rely On</tspan>
    </text>
    <path class="panel-orange" d="M0,488 Q0,476 12,476 H288 Q300,476 300,488 V600 H0 Z"/>
    <text class="offer" font-size="22" text-anchor="middle">
      <tspan x="150" y="512">5* Rated</tspan>
      <tspan x="150" y="546">Service &amp; No Broker Fees</tspan>
    </text>
    <rect class="cta-pill" x="108" y="562" width="84" height="23" rx="11.5"/>
    <text class="cta-label" x="150" y="578" text-anchor="middle">Click Here</text>
  </svg>
</div>
</body>
</html>
```